Dog grooming business card
This is a business card for m dog grooming business like it say above.
In the priorities box below I will have the text that I want on the card.

Industry/Entity Type

Business

Colors

Designer to choose colors to be used in the design.

Requirements
Must have
• My logo and the insurance stamp must be on the card.

Text it must have :

Professional grooming services
Email: lunabrisk@mailvale.net
Text or call 1 705 318 6052
TWF certified/member
Pet first aid certified
Next appointment ___________________________________
Nice to have
• Greens to match my logo

```html
<!DOCTYPE html>
<html lang="en">
<head>
<meta charset="utf-8">
<title>Luna Brisk – Grooming Business Card</title>
<link rel="stylesheet" href="https://fonts.googleapis.com/css2?family=Quattrocento:wght@400;700&family=Poiret+One&family=Open+Sans:wght@700;800&display=swap">
<style>
  :root {
    --leaf: #8cbf3f;
    --leaf-card: #9cc43c;
    --ink: #1d1d1b;
    --navy: #1f2a44;
    --paper: #ffffff;
    --stage-top: #ffffff;
    --stage-bottom: #c9dd9a;
    --edge: #9a9a9a;
  }
  html, body {
    margin: 0;
    padding: 0;
    width: 1200px;
    height: 1000px;
    overflow: hidden;
  }
  body {
    background: linear-gradient(180deg, var(--stage-top) 0%, var(--stage-bottom) 100%);
  }
  .stage { display: block; width: 1200px; height: 1000px; }
  .serif { font-family: 'Quattrocento', Georgia, serif; }
  .thin { font-family: 'Poiret One', 'Century Gothic', sans-serif; }
  .sans { font-family: 'Open Sans', Arial, sans-serif; font-weight: 800; }
  .brand-name { fill: var(--leaf); font-weight: 700; font-size: 40px; }
  .tagline { fill: var(--leaf); font-size: 32px; }
  .label { fill: var(--leaf); font-size: 22px; font-weight: 700; }
  .contact { fill: var(--ink); font-size: 25px; }
  .credential { fill: var(--ink); font-size: 23px; }
  .headline { fill: var(--paper); font-size: 26px; }
  .day { fill: var(--leaf); font-size: 14px; }
  .slot-label { fill: var(--navy); font-size: 14px; }
  .seal-name { fill: var(--paper); font-weight: 700; font-size: 24px; }
</style>
</head>
<body>
<svg class="stage" viewBox="0 0 1200 1000" xmlns="http://www.w3.org/2000/svg">

  <!-- Front of card -->
  <g class="card-front">
    <rect x="245" y="27" width="712" height="406" fill="var(--paper)" stroke="var(--edge)" stroke-width="1"/>
    <path d="M245 338 Q601 410 957 335 L957 433 L245 433 Z" fill="var(--leaf)"/>

    <text class="serif brand-name" x="601" y="150" text-anchor="middle">Luna Brisk</text>

    <text class="serif tagline" x="601" y="238" text-anchor="middle">Professional Grooming Services</text>

    <text x="601" y="300" text-anchor="middle">
      <tspan class="serif label">Email: </tspan><tspan class="thin contact" dx="6">lunabrisk@mailvale.net</tspan>
    </text>
    <text x="601" y="343" text-anchor="middle">
      <tspan class="serif label">Text or call: </tspan><tspan class="thin contact" dx="6" font-size="28">1 705 318 6052</tspan>
    </text>

    <text class="thin credential" x="445" y="407" text-anchor="middle">TWF certified/member</text>
    <text class="thin credential" x="767" y="407" text-anchor="middle">Pet first aid certified</text>
  </g>

  <!-- Back of card: appointment reminder -->
  <g class="card-back">
    <rect x="245" y="491" width="712" height="406" fill="var(--leaf-card)"/>

    <text class="sans headline" x="598" y="540" text-anchor="middle">YOUR NEXT APPOINTMENT IS ON:</text>

    <circle class="appointment-disc" cx="598" cy="723" r="165" fill="var(--paper)"/>

    <g class="weekday-picker">
      <circle cx="451" cy="584" r="26" fill="var(--paper)"/>
      <text class="sans day" x="451" y="589" text-anchor="middle">MON</text>
      <circle cx="408" cy="648" r="26" fill="var(--paper)"/>
      <text class="sans day" x="408" y="653" text-anchor="middle">TUE</text>
      <circle cx="396" cy="717" r="26" fill="var(--paper)"/>
      <text class="sans day" x="396" y="722" text-anchor="middle">WED</text>
      <circle cx="408" cy="783" r="26" fill="var(--paper)"/>
      <text class="sans day" x="408" y="788" text-anchor="middle">THU</text>
      <circle cx="441" cy="846" r="26" fill="var(--paper)"/>
      <text class="sans day" x="441" y="851" text-anchor="middle">FRI</text>
    </g>

    <g class="appointment-fields">
      <line x1="485" y1="660" x2="695" y2="660" stroke="var(--leaf)" stroke-width="2"/>
      <text class="sans slot-label" x="458" y="736">AT</text>
      <line x1="493" y1="736" x2="703" y2="736" stroke="var(--leaf)" stroke-width="2"/>
      <text class="sans slot-label" x="634" y="726">AM</text>
      <text class="sans slot-label" x="690" y="726">PM</text>
    </g>

    <g class="brand-seal">
      <circle cx="818" cy="700" r="78" fill="var(--paper)"/>
      <circle cx="818" cy="700" r="71" fill="var(--leaf-card)"/>
      <text class="serif seal-name" x="818" y="708" text-anchor="middle">Luna Brisk</text>
    </g>
  </g>
</svg>
</body>
</html>
```